Medical Billing Company Needs a Business Card Design

We need a business card design for a Florida based medical billing company called 'Clinicians Keystone Solutions'. We specialize in providing revenue cycle management services to physician and therapist offices (we're basically their back-office processing partner for providing billing software, claims submissions, A/R follow-up and patient statements & collections. Our logo is red and blue-ish, so make sure that whatever other elements are used will match appropriately. Our current business card design has a too small font size. I'd like to project an image that shows we are modern & reliable. On a side note, I'm planning on using ZUB for printing these cards.

Target Market(s)

Office managers, physicians, therapists

Industry/Entity Type

Printing

Requirements
Must have
• Logo
Name of Employee
Phone
Fax
E-mail
Website

```html
<!DOCTYPE html>
<html lang="en">
<head>
<meta charset="utf-8">
<title>Clinicians Keystone – Business Card</title>
<link href="https://fonts.googleapis.com/css2?family=Open+Sans:wght@400;600;700&display=swap" rel="stylesheet">
<style>
  :root {
    --page-bg: #ecebe8;
    --card-white: #ffffff;
    --brand-navy: #2c2a78;
    --brand-red: #a3141d;
    --brand-red-deep: #8a0d15;
    --brand-red-light: #c0424a;
    --text-dark: #3b3b45;
    --card-shadow: 0 10px 28px rgba(0, 0, 0, 0.18);
  }
  * { box-sizing: border-box; margin: 0; padding: 0; }
  html, body {
    width: 1200px;
    height: 720px;
    overflow: hidden;
  }
  body {
    background: var(--page-bg);
    font-family: "Open Sans", Arial, sans-serif;
    position: relative;
  }
  .card {
    position: absolute;
    top: 212px;
    width: 520px;
    height: 297px;
    border-radius: 4px;
    box-shadow: var(--card-shadow);
    overflow: hidden;
  }

  /* Front side */
  .card--front {
    left: 50px;
    background: var(--card-white);
  }
  .brand-name {
    position: absolute;
    left: 40px;
    top: 92px;
    font-size: 25px;
    font-weight: 600;
    letter-spacing: 2px;
    color: var(--brand-navy);
    display: flex;
    align-items: center;
    gap: 10px;
  }
  .brand-dot {
    width: 12px;
    height: 12px;
    border-radius: 50%;
    background: var(--brand-red);
  }
  .person {
    position: absolute;
    right: 26px;
    top: 108px;
    text-align: right;
  }
  .person__name {
    font-size: 17px;
    font-weight: 700;
    color: var(--brand-navy);
    line-height: 1.15;
  }
  .person__title {
    font-size: 12px;
    color: var(--brand-red);
  }
  .edge-tab {
    position: absolute;
    width: 12px;
    border-radius: 6px;
  }
  .edge-tab--right {
    right: -6px;
    top: 106px;
    height: 40px;
    background: var(--brand-red);
  }
  .edge-tab--left {
    left: -6px;
    top: 196px;
    height: 78px;
    background: var(--brand-navy);
  }
  .contact-list {
    position: absolute;
    left: 30px;
    top: 182px;
    list-style: none;
    font-size: 13px;
    color: var(--text-dark);
    line-height: 19px;
  }
  .contact-list li {
    display: flex;
    align-items: center;
    gap: 8px;
  }
  .contact-icon {
    width: 12px;
    height: 12px;
    fill: var(--brand-navy);
    flex: none;
  }
  .contact-list .address { padding-left: 20px; }

  /* Back side */
  .card--back {
    left: 630px;
    background: radial-gradient(circle at 50% 40%, var(--brand-red-light) 0%, var(--brand-red) 45%, var(--brand-red-deep) 100%);
    color: var(--card-white);
  }
  .back-brand {
    position: absolute;
    left: 0;
    right: 0;
    top: 100px;
    display: flex;
    justify-content: center;
    align-items: center;
    gap: 12px;
    font-size: 22px;
    font-weight: 600;
    letter-spacing: 3px;
  }
  .back-brand__circle {
    width: 14px;
    height: 14px;
    border: 2px solid var(--card-white);
    border-radius: 50%;
  }
  .back-url {
    position: absolute;
    left: 0;
    right: 0;
    bottom: 44px;
    text-align: center;
    font-size: 15px;
    letter-spacing: 3px;
  }
</style>
</head>
<body>

<section class="card card--front" aria-label="Business card front">
  <div class="brand-name"><span>CLINICIANS KEYSTONE</span><span class="brand-dot"></span></div>

  <div class="person">
    <p class="person__name">Your Name</p>
    <p class="person__title">Title</p>
  </div>
  <span class="edge-tab edge-tab--right"></span>
  <span class="edge-tab edge-tab--left"></span>

  <ul class="contact-list">
    <li>
      <svg class="contact-icon" viewBox="0 0 12 12" aria-hidden="true"><path d="M2.5 0.8 4.3 3.2 3.3 4.3C4 5.9 6.1 8 7.7 8.7L8.8 7.7 11.2 9.5 10.2 11.2C5.5 11 1 6.5 0.8 1.8Z"/></svg>
      <span>123-456-0789</span>
    </li>
    <li>
      <svg class="contact-icon" viewBox="0 0 12 12" aria-hidden="true"><path d="M3 0h6v12H3z M4 1.5v7h4v-7z" fill-rule="evenodd"/></svg>
      <span>123-456-0789</span>
    </li>
    <li>
      <svg class="contact-icon" viewBox="0 0 12 12" aria-hidden="true"><path d="M0 2h12v8H0z M1 3l5 3.5L11 3" fill-rule="evenodd"/><path d="M1 3l5 3.5L11 3" fill="none" stroke="#fff" stroke-width="1"/></svg>
      <span>info@clinicianskeystone.com</span>
    </li>
    <li>
      <svg class="contact-icon" viewBox="0 0 12 12" aria-hidden="true"><circle cx="6" cy="6" r="5.5"/><path d="M0.5 6h11M6 0.5c-3 3-3 8 0 11M6 0.5c3 3 3 8 0 11" fill="none" stroke="#fff" stroke-width="0.9"/></svg>
      <span>www.clinicianskeystone.com</span>
    </li>
    <li class="address">Street Name, City Name, State Zip Code</li>
  </ul>
</section>

<section class="card card--back" aria-label="Business card back">
  <div class="back-brand"><span class="back-brand__circle"></span><span>CLINICIANS KEYSTONE</span></div>
  <p class="back-url">www.clinicianskeystone.com</p>
</section>

</body>
</html>
```